Kestrel Facilities Business Card Design

We would now like to design business cards with the new Kestrel Facilities logo

Target Market(s)

Professional

Industry/Entity Type

Professional services

Contact Information for Business Card

Employee name, title, phone number, email address, corporate office address and logo.

Font styles to use
Sans Serif

Colors
0054AA
0677BA
7BADD7
CADEEF
E8F1F8

Requirements
Must have
• My logo
Should not have
• any other pictures or images besides my logo

```html
<!DOCTYPE html>
<html lang="en">
<head>
<meta charset="utf-8">
<title>Kestrel Facilities Business Card</title>
<link href="https://fonts.googleapis.com/css2?family=Montserrat:wght@400;500;600;700&display=swap" rel="stylesheet">
<style>
  :root {
    --navy: #0054AA;
    --blue: #0677BA;
    --sky: #7BADD7;
    --mist: #CADEEF;
    --frost: #E8F1F8;
    --ink: #3a3f45;
    --backdrop: #e4e1dc;
  }
  * { margin: 0; padding: 0; box-sizing: border-box; }
  html, body {
    width: 1200px; height: 887px; overflow: hidden;
    background: var(--backdrop);
    font-family: "Montserrat", sans-serif;
  }
  .card {
    position: absolute; left: 100px; top: 171px;
    width: 1000px; height: 545px;
    background: linear-gradient(135deg, #f3f7fb 0%, var(--frost) 55%, #dde9f3 100%);
    border: 1px solid #f7fafc;
    border-radius: 22px;
    box-shadow: 0 10px 30px rgba(0,0,0,0.10);
    overflow: hidden;
  }
  .holder { position: absolute; left: 76px; top: 62px; }
  .holder-name {
    font-size: 31px; font-weight: 600; color: var(--blue); letter-spacing: 0.2px;
  }
  .holder-title {
    font-size: 21px; font-weight: 500; color: var(--ink); margin-top: 2px; letter-spacing: 0.5px;
  }
  .website {
    position: absolute; left: 76px; top: 236px;
    font-size: 21px; font-weight: 500; color: var(--ink); letter-spacing: 0.6px;
  }
  .contact-band {
    position: absolute; left: 0; top: 288px;
    width: 622px; height: 184px;
    background: var(--blue);
    color: var(--frost);
    padding: 18px 0 0 76px;
  }
  .contact-line {
    display: flex; align-items: center; gap: 14px;
    font-size: 22px; font-weight: 500; letter-spacing: 0.6px; height: 33px;
  }
  .contact-line svg { width: 18px; height: 18px; flex: none; }
  .address {
    margin-top: 17px; font-size: 22px; font-weight: 500; line-height: 32px; letter-spacing: 0.6px;
  }
  .brand {
    position: absolute; left: 646px; top: 288px;
    width: 300px; height: 184px;
    display: flex; align-items: center; gap: 16px;
  }
  .brand-square { width: 26px; height: 26px; background: var(--navy); flex: none; }
  .brand-name {
    font-size: 40px; font-weight: 700; color: var(--navy); line-height: 1.05; text-transform: uppercase;
  }
</style>
</head>
<body>
  <div class="card">
    <div class="holder">
      <div class="holder-name">Daniel Whitford</div>
      <div class="holder-title">Director</div>
    </div>
    <div class="website">www.kestrelfacilities.com</div>

    <div class="contact-band">
      <div class="contact-line">
        <svg viewBox="0 0 24 24" aria-hidden="true"><path fill="currentColor" d="M6.6 10.8a15.1 15.1 0 0 0 6.6 6.6l2.2-2.2c.3-.3.7-.4 1-.2 1.1.4 2.3.6 3.6.6.6 0 1 .4 1 1V20c0 .6-.4 1-1 1C10.6 21 3 13.4 3 4c0-.6.4-1 1-1h3.5c.6 0 1 .4 1 1 0 1.3.2 2.5.6 3.6.1.3 0 .7-.2 1z"/></svg>
        <span>(555) 014-2290</span>
      </div>
      <div class="contact-line">
        <svg viewBox="0 0 24 24" aria-hidden="true"><rect x="3" y="5" width="18" height="14" fill="none" stroke="currentColor" stroke-width="2"/><path d="M3 6l9 7 9-7" fill="none" stroke="currentColor" stroke-width="2"/></svg>
        <span>info@kestrelfacilities.com</span>
      </div>
      <div class="address">1870 Alder Ridge Road<br>Salem, OR 97302</div>
    </div>

    <div class="brand">
      <div class="brand-square"></div>
      <div class="brand-name">Kestrel<br>Facilities</div>
    </div>
  </div>
</body>
</html>
```